Climbing Gear Company Stationary Design

We need some new stationary to standardise our business.
We require:

Business Card
A4 Letterhead
With complements slip

Our business is a Distributor and retailer of rock climbing equipment throughout Australia.
We need to the stationary (business card in particular) to reflect this.

Target Market(s)

customers, other retail outlets, overseas manufacturers.

Industry/Entity Type

Business

Requirements
Must have
• company logo
website url- www.ridgetopgearworks.com.au
email - mark@ridgetopgearworks.com
Business Address: Unit 3, 14-16 Marlowe Street, Tallowmere, VIC, 2371
Phone: 0438 627 194
my Name (on Business card) - Gordon Pellimore
use of Blue colour in our logo

```html
<!DOCTYPE html>
<html lang="en">
<head>
<meta charset="utf-8">
<title>Ridgetop Gearworks – Business Card</title>
<link href="https://fonts.googleapis.com/css2?family=Source+Sans+3:ital,wght@0,400;0,600;0,700;1,700&display=swap" rel="stylesheet">
<style>
  :root {
    --brand-blue: #22418b;
    --band-dark: #2a2a2a;
    --band-light: #8c8c8c;
    --paper: #ffffff;
    --rule-grey: #c9c9c9;
    --text-grey: #333333;
    --backdrop: #e6e4e1;
  }
  * { margin: 0; padding: 0; box-sizing: border-box; }
  html, body { width: 1200px; height: 440px; overflow: hidden; }
  body {
    background: var(--backdrop);
    font-family: "Source Sans 3", "Segoe UI", Arial, sans-serif;
    position: relative;
  }
  .card {
    position: absolute;
    top: 60px;
    width: 533px;
    height: 305px;
    border-radius: 22px;
    overflow: hidden;
  }
  .card-front { left: 55px; background: var(--paper); }
  .card-back { left: 611px; background: var(--brand-blue); }

  .wordmark {
    color: var(--brand-blue);
    font-weight: 700;
    text-transform: uppercase;
    letter-spacing: 2px;
    white-space: nowrap;
    line-height: 1;
  }
  .tagline {
    color: var(--brand-blue);
    font-weight: 600;
    text-transform: uppercase;
    letter-spacing: 5px;
    white-space: nowrap;
    line-height: 1;
  }

  .card-front .wordmark { position: absolute; left: 40px; top: 42px; font-size: 39px; }
  .card-front .tagline { position: absolute; left: 41px; top: 89px; font-size: 16px; }
  .front-rule {
    position: absolute; left: 40px; top: 118px;
    width: 432px; height: 1px; background: var(--rule-grey);
  }
  .website {
    position: absolute; right: 61px; top: 125px;
    font-size: 13px; color: var(--text-grey);
  }

  .contact-band { position: absolute; left: 0; top: 180px; width: 533px; height: 90px; }
  .holder-name {
    position: absolute; left: 21px; top: 215px;
    font-size: 20px; font-weight: 700; font-style: italic;
    color: var(--paper); text-transform: uppercase; letter-spacing: 0.2px;
  }
  .contact-list {
    position: absolute; left: 304px; top: 187px;
    color: var(--paper); font-size: 13.5px; line-height: 17px;
    list-style: none;
  }
  .contact-list li { display: flex; align-items: center; gap: 6px; }
  .contact-list svg { width: 11px; height: 11px; flex: none; }
  .contact-list .divider {
    height: 1px; width: 196px; background: rgba(255,255,255,0.55);
    margin: 5px 0 6px;
  }

  .back-band {
    position: absolute; left: 0; top: 148px;
    width: 100%; height: 110px; background: var(--paper);
  }
  .card-back .wordmark { position: absolute; left: 56px; top: 19px; font-size: 39px; }
  .card-back .tagline { position: absolute; left: 58px; top: 65px; font-size: 16px; }
</style>
</head>
<body>
  <section class="card card-front" aria-label="Business card front">
    <div class="wordmark">Ridgetop Gearworks</div>
    <div class="tagline">The Rope•The Rock•The Summit</div>
    <div class="front-rule"></div>
    <div class="website">www.ridgetopgearworks.com.au</div>

    <svg class="contact-band" viewBox="0 0 533 90" aria-hidden="true">
      <defs>
        <linearGradient id="nameBandShade" x1="0" x2="1" y1="0" y2="0">
          <stop offset="0" stop-color="var(--band-dark)"/>
          <stop offset="1" stop-color="var(--band-light)"/>
        </linearGradient>
      </defs>
      <polygon points="0,0 281,0 214,90 0,90" fill="url(#nameBandShade)"/>
      <polygon points="291,0 533,0 533,90 224,90" fill="var(--brand-blue)"/>
    </svg>

    <div class="holder-name">Gordon Pellimore</div>

    <ul class="contact-list">
      <li>
        <svg viewBox="0 0 12 12" aria-hidden="true"><path d="M3 1 L5 3.5 L4 5 Q5.5 7.5 7.5 8.5 L9 7.5 L11 9.5 L9.5 11 Q5 10.5 1.5 4 Q1.5 2 3 1Z" fill="#fff"/></svg>
        0438 627 194
      </li>
      <li>
        <svg viewBox="0 0 12 12" aria-hidden="true"><rect x="1" y="3" width="10" height="7" fill="none" stroke="#fff" stroke-width="1.2"/><path d="M1 3 L6 7 L11 3" fill="none" stroke="#fff" stroke-width="1.2"/></svg>
        mark@ridgetopgearworks.com
      </li>
      <li class="divider" aria-hidden="true"></li>
      <li>Unit 3, 14-16 Marlowe Street</li>
      <li>Tallowmere, VIC, 2371</li>
    </ul>
  </section>

  <section class="card card-back" aria-label="Business card back">
    <div class="back-band">
      <div class="wordmark">Ridgetop Gearworks</div>
      <div class="tagline">The Rope•The Rock•The Summit</div>
    </div>
  </section>
</body>
</html>
```